Vision, Mission and Culture Posters

We have written text paragraphs for our company vision and mission and need them made into a2 or a3 sized posters using our logo for inspiration for colour. Our company culture has 10 paragraphs and we'd like this to be a single poster of a2 or a1. Each poster should have the logo on and share common design. It's not a complex job really.

Industry/Entity Type

It Company

Requirements
Nice to have
• These will be going up on our office wall so need to be clear to read from a distance and look professional but also not stodgy.

```html
<!DOCTYPE html>
<html lang="en">
<head>
<meta charset="utf-8">
<title>Kerbside Lets – Company Values</title>
<link rel="stylesheet" href="https://fonts.googleapis.com/css2?family=Open+Sans:wght@400;700&family=Source+Sans+3:wght@700&display=swap">
<style>
  :root {
    --header-dark: #3a0d0d;
    --header-red: #e4262b;
    --header-bright: #f23a36;
    --paper-top: #fbf6a4;
    --paper-bottom: #fff200;
    --badge-yellow: #ffee00;
    --heading-red: #9b1b1b;
    --body-ink: #222222;
    --rule: #a8a49a;
    --white: #ffffff;
  }
  html, body {
    margin: 0;
    padding: 0;
    overflow: hidden;
  }
  body {
    width: 848px;
    height: 1200px;
    background: var(--white);
  }
  .poster {
    position: relative;
    width: 848px;
    height: 1200px;
    overflow: hidden;
    font-family: "Open Sans", Arial, sans-serif;
    background: linear-gradient(180deg, var(--paper-top) 0%, #fcf57a 50%, var(--paper-bottom) 100%);
  }
  .poster-header {
    position: absolute;
    left: 0; top: 0;
    width: 848px;
    height: 122px;
    background: linear-gradient(100deg, var(--header-dark) 0%, #8a1616 22%, var(--header-red) 55%, var(--header-bright) 100%);
  }
  .poster-title {
    position: absolute;
    left: 37px;
    top: 30px;
    margin: 0;
    font-family: "Source Sans 3", "Open Sans", sans-serif;
    font-weight: 700;
    font-size: 31px;
    line-height: 36px;
    color: var(--white);
  }
  .brand {
    position: absolute;
    left: 552px;
    top: 34px;
    display: flex;
    align-items: center;
    gap: 12px;
  }
  .brand-mark {
    width: 30px;
    height: 30px;
    background: var(--badge-yellow);
  }
  .brand-name {
    font-family: "Source Sans 3", "Open Sans", sans-serif;
    font-weight: 700;
    font-size: 26px;
    color: var(--white);
  }
  .value {
    position: absolute;
    left: 0;
    width: 848px;
    box-sizing: border-box;
    padding: 8px 36px 0 37px;
    border-bottom: 2px solid var(--rule);
  }
  .value:last-child { border-bottom: none; }
  .value-title {
    margin: 0;
    font-weight: 700;
    font-size: 14.5px;
    line-height: 19px;
    color: var(--heading-red);
  }
  .value-text {
    margin: 0;
    font-size: 14.2px;
    line-height: 19.2px;
    color: var(--body-ink);
    text-align: justify;
  }
</style>
</head>
<body>
<main class="poster">
  <header class="poster-header">
    <h1 class="poster-title">Kerbside Lets –<br>Company Values</h1>
    <div class="brand">
      <span class="brand-mark"></span>
      <span class="brand-name">Kerbside Lets</span>
    </div>
  </header>

  <section class="value" style="top:122px;height:112px">
    <h2 class="value-title">1. Communication</h2>
    <p class="value-text">&nbsp;We believe in open communication providing our customers, colleagues and others with honest, accurate, concise and prompt information relevant to their needs to ensure everyone always has a sound understanding of any matter being communicated. We are polite, friendly and warm and we use good communication as a means of enhancing our customer experience.</p>
  </section>

  <section class="value" style="top:234px;height:110px">
    <h2 class="value-title">2. Education</h2>
    <p class="value-text">&nbsp;We believe in the importance of continual learning and education and thrive on helping our colleagues by sharing our knowledge and learnings. We learn from our mistakes and use them to build a better, stronger, closer team environment. Understanding that everyone's needs are different and that we learn in different ways, we challenge our people to constantly improve their professional development in a way that works best for them.</p>
  </section>

  <section class="value" style="top:344px;height:110px">
    <h2 class="value-title">3. Professionalism</h2>
    <p class="value-text">&nbsp;We represent ourselves as professionals and our business to the best of our abilities at all times taking particular care to give the best impression of ourselves to those we interact with during the course of our working days whether that be by phone, email or in person. We are always on time, well presented, well prepared and work hard to succeed.</p>
  </section>

  <section class="value" style="top:454px;height:68px">
    <h2 class="value-title">4. Ownership</h2>
    <p class="value-text">&nbsp;We are each fully responsible for our roles and for our contribution to the success of our business. We are accountable for our results, our ability to improve at what we do, our mistakes and what we do to correct them.</p>
  </section>

  <section class="value" style="top:522px;height:110px">
    <h2 class="value-title">5. Commercial Awareness</h2>
    <p class="value-text">&nbsp;We understand that in a small business everything we do can impact the success of our business and we commit ourselves to thinking about the impact on our business of all the decisions we make before we make them. We consider cost against benefit, remembering the cheapest option doesn't always give the greatest benefit, the best value use of our time, who benefits from what we do and how it benefits our business.</p>
  </section>

  <section class="value" style="top:632px;height:110px">
    <h2 class="value-title">6. Balance</h2>
    <p class="value-text">&nbsp;We try to find the best balance in our lives between our responsibilities, obligations, duties and desires whilst still ensuring we have time to devote to friends, families, fun and life. We try to balance our opinions and thoughts with those of others and believe that with balance comes fairness, integrity, self-control and a great attitude.</p>
  </section>

  <section class="value" style="top:742px;height:110px">
    <h2 class="value-title">7. Customer Service</h2>
    <p class="value-text">&nbsp;We believe that without our customers we would not be successful and understand the outstanding level of service we give them is critical to our continued success, even down to the smallest action whenever that may be required from us. We go out of our way to help any customer with an issue and are only satisfied when we have helped them achieve a fair outcome they are happy with.</p>
  </section>

  <section class="value" style="top:852px;height:92px">
    <h2 class="value-title">8. Consistency</h2>
    <p class="value-text">&nbsp;We believe in consistency of our work, our approach, our positive attitude and our actions to set a standard at which our colleagues and customers feel a level of familiarity that strengthens our relationship whilst representing ourselves and our business to their best.</p>
  </section>

  <section class="value" style="top:944px;height:90px">
    <h2 class="value-title">9. Success</h2>
    <p class="value-text">We understand success isn't given, it is earned every day, piece by piece. We are driven to succeed as an individual and as a team and we support each other in earning that success. We are not afraid to celebrate our successes to acknowledge our hard work and dedication to our achieving our goals.</p>
  </section>

  <section class="value" style="top:1034px;height:166px">
    <h2 class="value-title">10. Commitment</h2>
    <p class="value-text">We are committed to the company vision, to the mission and to upholding the company culture as well as showing the company the same commitment it has shown to us. We talk about our vision, mission and culture often, use them to help guide ourselves and our colleagues as we go about our work. We are not afraid to let our colleagues know when we feel they are not showing the right commitment to our vision, mission and culture but make sure we do so in a positive and helpful way to ensure they can get back on track as easily as possible.</p>
  </section>
</main>
</body>
</html>
```